Business card design Needed for new logo / Construction business, home extensions and new builds

We need a business card design using our new logo files which i will attach to this project :)

We are a small construction business specialising in home extensions, new builds and property development. We are very ambitious and would appreciate professional and elegant designs for our new business card.

Very serious about using the services on MakerQuarry and recently acquired our new logo from here :)

Please get involved, i will feedback when i can as i am very busy but can respond daily, thanks

Target Market(s)

People that want to build onto their houses, new building developments or adding too their existing property

Industry/Entity Type

Construction

Contact Information for Business Card

Renwick Tolliver Construction, Lionel Ashby (Managing Director), Tel 07822254961, email - info@renwick-tolliver, www.renwick-tolliver.co.uk

Colors

Designer to choose colors to be used in the design.

Requirements
Must have
• I like a deep grey on the back please. A lot of you have provided black from and back, try mixing things up a little. The black looks cool 😎 Thanks

```html
<!DOCTYPE html>
<html lang="en">
<head>
<meta charset="utf-8">
<title>Renwick Tolliver Construction – Business Card</title>
<link href="https://fonts.googleapis.com/css2?family=Cinzel:wght@500&family=Tinos&display=swap" rel="stylesheet">
<style>
  :root {
    --stage: #1c1c1c;
    --card-front: #ffffff;
    --card-back: #666666;
    --gold: #c8952a;
    --ink: #3a3a3a;
    --back-mark: #3e3e3e;
  }
  * { margin: 0; padding: 0; box-sizing: border-box; }
  html, body { width: 1200px; height: 1200px; overflow: hidden; }
  body {
    background: var(--stage);
    display: flex;
    align-items: center;
    justify-content: center;
    gap: 60px;
  }
  .card {
    width: 440px;
    height: 760px;
    border-radius: 36px;
    position: relative;
  }
  .card--front {
    background: var(--card-front);
    display: flex;
    flex-direction: column;
    align-items: center;
    text-align: center;
  }
  .brand {
    margin-top: 150px;
    display: flex;
    flex-direction: column;
    align-items: center;
    gap: 18px;
  }
  .brand__square {
    width: 22px;
    height: 22px;
    background: var(--gold);
  }
  .brand__name {
    font-family: "Cinzel", serif;
    font-weight: 500;
    color: var(--gold);
    font-size: 25px;
    line-height: 1.35;
    letter-spacing: 1px;
  }
  .person {
    margin-top: 190px;
  }
  .person__name {
    font-family: "Cinzel", serif;
    font-weight: 500;
    color: var(--gold);
    font-size: 30px;
    letter-spacing: 1px;
  }
  .person__title {
    font-family: "Tinos", serif;
    color: var(--ink);
    font-size: 20px;
    margin-top: 4px;
  }
  .contact-icons {
    display: flex;
    gap: 12px;
    margin-top: 26px;
  }
  .contact-icons svg { width: 26px; height: 26px; }
  .contact-list {
    list-style: none;
    margin-top: 22px;
    font-family: "Tinos", serif;
    color: var(--ink);
    font-size: 20px;
    line-height: 1.5;
  }
  .card--back {
    background: var(--card-back);
    display: flex;
    flex-direction: column;
    align-items: center;
    justify-content: center;
    gap: 22px;
  }
  .back-mark__square {
    width: 34px;
    height: 34px;
    background: var(--back-mark);
  }
  .back-mark__name {
    font-family: "Cinzel", serif;
    font-weight: 500;
    color: var(--back-mark);
    font-size: 34px;
    line-height: 1.3;
    text-align: center;
  }
</style>
</head>
<body>
  <section class="card card--front">
    <div class="brand">
      <span class="brand__square"></span>
      <p class="brand__name">Renwick Tolliver<br>Construction</p>
    </div>
    <div class="person">
      <h1 class="person__name">Lionel Ashby</h1>
      <p class="person__title">Managing Director</p>
    </div>
    <div class="contact-icons">
      <svg viewBox="0 0 26 26" aria-label="Phone">
        <circle cx="13" cy="13" r="11.5" fill="none" stroke="#c8952a" stroke-width="1.5"/>
        <path d="M9 8.5c0 5 3.5 8.5 8.5 8.5l1-2-2.3-1.2-1 1c-1.6-.7-2.8-1.9-3.5-3.5l1-1L11.5 7.5z" fill="#c8952a"/>
      </svg>
      <svg viewBox="0 0 26 26" aria-label="Email">
        <circle cx="13" cy="13" r="11.5" fill="none" stroke="#c8952a" stroke-width="1.5"/>
        <rect x="7.5" y="9" width="11" height="8" fill="#c8952a"/>
        <path d="M7.5 9l5.5 4.5L18.5 9" fill="none" stroke="#fff" stroke-width="1"/>
      </svg>
      <svg viewBox="0 0 26 26" aria-label="Website">
        <circle cx="13" cy="13" r="11.5" fill="none" stroke="#c8952a" stroke-width="1.5"/>
        <circle cx="13" cy="13" r="5.5" fill="none" stroke="#c8952a" stroke-width="1.3"/>
        <path d="M7.5 13h11M13 7.5c-2.5 3-2.5 8 0 11M13 7.5c2.5 3 2.5 8 0 11" fill="none" stroke="#c8952a" stroke-width="1"/>
      </svg>
    </div>
    <ul class="contact-list">
      <li>07822254961</li>
      <li>info@renwick-tolliver</li>
      <li>www.renwick-tolliver.co.uk</li>
    </ul>
  </section>

  <section class="card card--back">
    <span class="back-mark__square"></span>
    <p class="back-mark__name">Renwick Tolliver</p>
  </section>
</body>
</html>
```